uk based ecommerce website requires fresh look ,high quality look and feel

we are a web based company selling eco friendly ground reinforcement grids to diy and construction sectors
our existing website is www.pondermeshpaths.co.uk ,

we have already updated the logo so that is the branding sorted .so we need a ecommerce website that is very much up-to date in design and layout and which has content management system for ease of use so that we can add products and information as required.

Use current logo as reference for colour scheme.
www.pondermeshpaths.co.uk

The current website has 6 pages accessible through the navigation bar, I would now like 5 pages, removing the need for the Trade Enquiries page possibly have it with along with contact us.

Target Market(s)

construction industry , diy end users,
retail market, landscapers, gardeners

Industry/Entity Type

Construction

Font styles to use
Other font styles liked:
• logo font prometo

Colors
f78f20
9bcb3c

Requirements
Must have
• logo colours and logo design in website with cms responsive design for tablet and mobile devices
• expect content to work flawlessly and look great across all devices
• HTML 5 custom design with coding as required
• must have good experiance in ecommerce website design
• eye catching, high quality look and feel and very user friedly ,very up-to date.
Nice to have
• picture slider show
• explain in writing what exactly i am getting in my ecommerce website
Should not have
• plain , basic design , old fashion looking ,cheap look

```html
<!DOCTYPE html>
<html lang="en">
<head>
<meta charset="utf-8">
<title>Pondermesh Ground Solutions – Shop</title>
<link rel="stylesheet" href="https://fonts.googleapis.com/css2?family=Exo+2:wght@400;500;600;700;800&family=Open+Sans:wght@400;600;700&display=swap">
<style>
:root{
  --orange:#f78f20;
  --orange-deep:#e8601c;
  --green:#9bcb3c;
  --green-dark:#5e9a2c;
  --header:#2f2f2f;
  --footer:#333333;
  --panel:#ececec;
  --line:#d6d6d6;
  --ink:#3a3a3a;
  --muted:#6a6a6a;
  --white:#ffffff;
  --head-font:"Exo 2", sans-serif;
  --body-font:"Open Sans", sans-serif;
}
*{box-sizing:border-box;margin:0;padding:0}
html,body{width:1200px;height:2356px;overflow:hidden}
body{position:relative;background:var(--white);font-family:var(--body-font);color:var(--ink);font-size:12px}
.abs{position:absolute}
ul{list-style:none}

/* header */
.topbar{left:0;top:0;width:1200px;height:97px;background:var(--header)}
.navbar{left:0;top:97px;width:1200px;height:52px;background:var(--green);border-bottom:3px solid #b9dc6a}
.brand{left:122px;top:0;width:184px;height:136px;background:var(--white);clip-path:polygon(0 0,100% 0,100% 84%,50% 100%,0 84%);box-shadow:0 2px 6px rgba(0,0,0,.3);z-index:3}
.brand-mark{left:16px;top:32px;width:26px;height:26px;border-radius:50%;background:var(--green)}
.brand-name{left:48px;top:30px;font-family:var(--head-font);font-weight:800;font-size:19px;color:var(--orange);letter-spacing:-.2px}
.brand-tag{left:48px;top:54px;font-family:var(--head-font);font-weight:600;font-size:11px;color:var(--green-dark);letter-spacing:.3px}
.welcome{left:327px;top:9px;color:#e8e8e8;font-size:11px;font-style:italic}
.account-links{top:9px;left:860px;display:flex;gap:24px;color:#cfcfcf;font-size:11px}
.account-links span{display:flex;align-items:center;gap:5px}
.account-links .login{color:var(--green)}
.hotline{left:327px;top:42px;color:var(--white);font-family:var(--head-font);font-weight:600;font-size:14px}
.hotline .badge{display:inline-block;background:var(--green);color:var(--header);font-weight:800;padding:0 3px;margin-right:4px;font-size:13px}
.hotline-nums{left:352px;top:62px;color:var(--green);font-family:var(--head-font);font-weight:600;font-size:16px}
.hotline-nums i{font-style:normal;color:var(--green);margin:0 6px}
.search{left:617px;top:50px;width:319px;height:28px;display:flex;border-radius:3px;overflow:hidden}
.search .field{flex:1;background:var(--white);color:#aaa;font-size:10px;font-style:italic;padding:8px 10px}
.search .btn{width:86px;background:var(--orange);color:var(--white);font-family:var(--head-font);font-weight:600;font-size:12px;text-align:center;line-height:28px}
.cart{left:953px;top:50px;width:136px;height:28px;display:flex;border-radius:3px;overflow:hidden;font-family:var(--head-font);font-size:12px;color:var(--white)}
.cart .label{flex:1;background:var(--green);display:flex;align-items:center;gap:6px;padding-left:10px;font-weight:600}
.cart .label small{font-size:10px;font-weight:400}
.cart .cur{width:22px;background:var(--orange);text-align:center;line-height:28px;font-weight:700}
.nav{left:310px;top:97px;height:52px;display:flex;font-family:var(--head-font);font-size:15px;font-weight:500;color:var(--white)}
.nav a{display:block;height:52px;line-height:52px;padding:0 17px;color:inherit;text-decoration:none}
.nav a.active{background:#87b52d}

/* categories */
.categories{left:97px;top:170px;width:233px}
.cat-head{height:34px;background:var(--orange);color:var(--white);font-family:var(--head-font);font-weight:600;font-size:14px;display:flex;align-items:center;gap:8px;padding-left:12px}
.cat-list li{height:34.4px;background:var(--panel);border-top:1px solid var(--white);display:flex;align-items:center;justify-content:space-between;padding:0 10px 0 12px;font-size:11.5px;color:var(--muted)}
.cat-list li.current{color:var(--orange)}

/* hero slider */
.slider{left:338px;top:170px;width:757px;height:298px;border:4px solid var(--white);box-shadow:0 0 4px rgba(0,0,0,.3)}
.slider .photo{position:absolute;inset:0;background:radial-gradient(ellipse at 40% 40%,#b8a488 0%,#8f7a60 45%,#4a4036 100%)}
.slide-caption{left:10px;top:24px;background:rgba(40,40,40,.75);color:var(--white);font-family:var(--head-font);font-weight:600;font-size:15px;padding:6px 14px;letter-spacing:.3px}
.slide-arrow{top:135px;color:var(--white);font-size:22px;font-weight:700}
.slide-dots{right:10px;bottom:10px;background:rgba(40,40,40,.7);padding:4px 6px;border-radius:8px;display:flex;gap:4px}
.slide-dots b{width:7px;height:7px;border-radius:50%;background:#999}
.slide-dots b.on{background:var(--white)}
.promo{left:338px;top:476px;width:757px;height:101px;background:linear-gradient(90deg,#35502a 0%,#4e7a2c 45%,#6a9b34 70%,#3f8a3a 100%)}
.promo h2{position:absolute;left:40px;top:24px;font-family:var(--head-font);font-weight:600;font-size:24px;color:var(--white);letter-spacing:.2px}
.promo p{position:absolute;left:40px;top:55px;font-size:13px;color:#eaeaea}
.promo .shop{position:absolute;left:571px;top:38px;width:96px;height:30px;background:var(--orange);color:var(--white);font-family:var(--head-font);font-weight:600;font-size:12px;text-align:center;line-height:30px;border-radius:2px}

/* panels */
.panel{background:var(--panel)}
.panel-title{position:absolute;left:12px;top:13px;font-family:var(--head-font);font-weight:700;font-size:14px;color:var(--ink);letter-spacing:.2px}
.panel-title em{font-style:normal;color:var(--orange)}
.panel-rule{position:absolute;left:12px;right:12px;top:36px;height:1px;background:#d0d0d0}
.pager{position:absolute;top:12px;right:12px;display:flex;gap:3px}
.pager span{width:16px;height:16px;border-radius:50%;border:1px solid #8a8a8a;font-size:10px;line-height:14px;text-align:center;color:#555}
.pager span:first-child{border-color:#bbb;color:#bbb}

.news{left:97px;top:598px;width:233px;height:384px}
.news .photo{position:absolute;left:10px;top:51px;width:215px;height:111px;background:linear-gradient(180deg,#c9d6de 0%,#9aa79c 45%,#6f7a58 70%,#8a8780 100%)}
.news h3{position:absolute;left:10px;top:171px;font-family:var(--head-font);font-weight:700;font-size:12px;color:var(--orange)}
.news .meta{position:absolute;left:10px;top:201px;width:215px;font-size:11px;color:var(--muted);line-height:19px}
.news .likes{position:absolute;right:0;top:19px;color:var(--orange)}
.news p{position:absolute;left:10px;top:249px;width:215px;font-size:11px;line-height:14.6px;color:var(--muted);text-align:justify}
.read-more{font-family:var(--head-font);font-weight:700;font-size:11px;color:var(--orange)}
.news .read-more{position:absolute;left:10px;top:362px}

.popular{left:97px;top:1007px;width:233px;height:383px}
.popular .hex{position:absolute;left:38px;top:40px}
.popular .name{position:absolute;left:0;width:233px;top:250px;text-align:center;font-size:11px;color:var(--ink);line-height:13px}
.popular .price{position:absolute;left:0;width:233px;top:290px;text-align:center;font-weight:700;font-size:20px}
.deal{position:absolute;left:0;top:325px;width:233px;height:32px;display:flex;font-family:var(--head-font);font-weight:600;font-size:13px;color:var(--white)}
.deal .order{width:122px;background:var(--green);text-align:center;line-height:32px;clip-path:polygon(0 0,100% 0,93% 100%,0 100%)}
.deal .off{flex:1;margin-left:-4px;background:var(--orange);text-align:center;line-height:32px;clip-path:polygon(8% 0,100% 0,100% 100%,0 100%)}

.products{left:338px;width:765px}
.products.new{top:598px;height:792px}
.products.featured{top:1437px;height:385px}
.grid{position:absolute;left:18px;top:66px;display:grid;grid-template-columns:repeat(3,240px);row-gap:44px}
.card{width:240px;text-align:center;position:relative}
.card svg{display:block;margin:0 auto}
.card .name{height:32px;margin-top:10px;font-size:11px;line-height:13px;color:var(--ink);display:flex;align-items:center;justify-content:center}
.card .buy{margin-top:0;display:flex;justify-content:center;gap:6px;font-family:var(--head-font);font-weight:600;color:var(--white)}
.card .shop{width:86px;height:33px;line-height:33px;font-size:12px;background:var(--green);clip-path:polygon(0 0,100% 0,92% 100%,0 100%)}
.card .price{width:88px;height:33px;line-height:33px;font-size:14px;background:var(--orange);clip-path:polygon(8% 0,100% 0,100% 100%,0 100%)}
.hover-tag{position:absolute;left:0;width:240px;top:80px;color:var(--white);font-size:13px;text-align:center;line-height:17px}
.hover-tag small{display:block;font-size:11px;text-decoration:underline}

.stripe{height:8px;background:linear-gradient(90deg,var(--green-dark) 0 25%,var(--green) 25% 50%,var(--orange) 50% 75%,var(--orange-deep) 75% 100%)}

.testimonials{left:97px;top:1437px;width:233px;height:385px}
.testimonials .avatar{position:absolute;left:64px;top:52px}
.testimonials .quote{position:absolute;left:0;width:233px;top:183px;text-align:center;font-size:26px;font-weight:700;color:#555;line-height:20px}
.testimonials p{position:absolute;left:10px;top:215px;width:215px;font-size:11px;line-height:14.6px;color:var(--muted)}
.testimonials .who{position:absolute;left:10px;top:300px;font-size:11px;line-height:15px;color:var(--ink)}
.testimonials .who b{font-weight:600}

/* about & clients */
.section-head{font-family:var(--head-font);font-weight:700;font-size:14px;color:var(--ink)}
.section-head em{font-style:normal;color:var(--orange)}
.about{left:107px;top:1852px;width:223px}
.about .section-head{padding-bottom:4px;border-bottom:2px solid;border-image:linear-gradient(90deg,var(--orange) 0 50%,var(--green) 50% 100%) 1}
.about p{margin-top:12px;font-size:11px;line-height:14.6px;color:var(--muted);text-align:justify}
.about .read-more{display:block;margin-top:10px}
.clients{left:353px;top:1852px;width:748px}
.clients .section-head{padding-bottom:4px;border-bottom:2px solid;border-image:linear-gradient(90deg,var(--orange) 0 20%,var(--green) 20% 40%,var(--orange) 40% 60%,var(--green) 60% 80%,var(--orange) 80% 100%) 1}
.client-row{position:absolute;top:52px;left:0;width:748px;height:60px}
.client{position:absolute;top:8px;font-family:var(--body-font);font-weight:600;font-size:30px;color:#5a5a5a;line-height:32px;text-align:center}
.client small{display:block;font-size:7px;letter-spacing:1px;line-height:10px;text-transform:uppercase;color:#5a5a5a}
.client-arrow{position:absolute;top:14px;font-size:24px;color:#bbb}

/* newsletter & footer */
.footer{left:0;top:2042px;width:1200px;height:259px;background:var(--footer)}
.newsletter{left:97px;top:2003px;width:1006px;height:78px;background:var(--orange)}
.newsletter h2{position:absolute;left:27px;top:24px;font-family:var(--head-font);font-weight:500;font-size:21px;color:var(--white)}
.newsletter .field{position:absolute;left:236px;top:25px;width:225px;height:30px;background:var(--white);font-size:10px;font-style:italic;color:#aaa;padding:9px 8px}
.newsletter .btn{position:absolute;left:461px;top:25px;width:94px;height:30px;background:var(--green);color:var(--white);font-family:var(--head-font);font-weight:600;font-size:11px;line-height:30px;text-align:center}
.social{position:absolute;top:20px;left:781px;display:flex;gap:10px}
.foot-col h3{font-family:var(--head-font);font-weight:500;font-size:15px;color:var(--green);padding-bottom:5px;border-bottom:1px dashed #777}
.sitemap{left:113px;top:2120px;width:255px}
.sitemap .cols{display:flex;margin-top:10px}
.sitemap ul{width:118px;padding-left:12px}
.sitemap li{font-size:11px;line-height:16.3px;color:#cfcfcf;position:relative}
.sitemap li::before{content:"";position:absolute;left:-10px;top:7px;width:3px;height:3px;border-radius:50%;background:#cfcfcf}
.sitemap li.current{color:var(--green);font-weight:600}
.portfolio{left:394px;top:2120px;width:230px}
.thumbs{margin-top:12px;display:grid;grid-template-columns:repeat(4,48px);gap:6px 8px}
.thumbs div{height:46px}
.portfolio .view{margin-top:8px;text-align:center;font-size:11px;color:var(--green)}
.contact{left:650px;top:2120px;width:240px}
.contact li{display:flex;gap:8px;font-size:11px;line-height:15px;color:#cfcfcf;margin-top:9px}
.cards{display:flex;gap:5px;margin-top:14px}
.cards span{width:39px;height:20px;background:var(--white);border-radius:2px;font-size:8px;font-weight:600;color:#555;text-align:center;line-height:20px}
.service{left:916px;top:2112px;width:160px}
.service .big{font-family:var(--head-font);font-weight:800;font-size:44px;color:var(--white);line-height:44px;text-align:center}
.service .big em{font-style:normal;color:var(--orange)}
.service .tag{margin:4px auto 0;width:140px;background:var(--white);color:#222;font-family:var(--head-font);font-weight:800;font-size:12px;text-align:center;padding:3px 0}
.service .nums{margin-top:34px;font-family:var(--head-font);font-weight:700;font-size:16px;color:var(--green);line-height:21px;text-align:center}
.bottom-stripe{left:0;top:2301px;width:1200px}
.copyright{left:0;top:2309px;width:1200px;height:47px;background:var(--green);font-size:11px;color:#2f3b17;padding:17px 0 0 107px}
</style>
</head>
<body>

<svg width="0" height="0" class="abs" aria-hidden="true">
  <defs>
    <linearGradient id="turf" x1="0" y1="0" x2="0" y2="1">
      <stop offset="0" stop-color="#8fb447"/><stop offset=".3" stop-color="#6f8f3a"/><stop offset=".45" stop-color="#7a5a3c"/><stop offset=".7" stop-color="#2f8a4a"/><stop offset="1" stop-color="#1f6e38"/>
    </linearGradient>
    <linearGradient id="mesh" x1="0" y1="0" x2="1" y2="1">
      <stop offset="0" stop-color="#3a3a3a"/><stop offset=".5" stop-color="#262626"/><stop offset="1" stop-color="#1b1b1b"/>
    </linearGradient>
    <linearGradient id="tyre" x1="0" y1="0" x2="1" y2="1">
      <stop offset="0" stop-color="#2a2a2a"/><stop offset=".45" stop-color="#555"/><stop offset=".7" stop-color="#9a9a9a"/><stop offset="1" stop-color="#c9c9c9"/>
    </linearGradient>
    <radialGradient id="gravel" cx=".5" cy=".5" r=".6">
      <stop offset="0" stop-color="#b7a286"/><stop offset=".6" stop-color="#8d7a64"/><stop offset="1" stop-color="#5a4d40"/>
    </radialGradient>
    <radialGradient id="portrait" cx=".5" cy=".4" r=".6">
      <stop offset="0" stop-color="#c8a58a"/><stop offset="1" stop-color="#7a6a5e"/>
    </radialGradient>
  </defs>
</svg>

<!-- header -->
<header>
  <div class="abs topbar"></div>
  <div class="abs navbar"></div>
  <div class="abs brand">
    <span class="abs brand-mark"></span>
    <span class="abs brand-name">PONDERMESH</span>
    <span class="abs brand-tag">GROUND SOLUTIONS</span>
  </div>
  <div class="abs welcome">Welcome Message for site visiter.....</div>
  <div class="abs account-links">
    <span><svg width="9" height="10" viewBox="0 0 9 10"><circle cx="4.5" cy="3" r="2.5" fill="#cfcfcf"/><path d="M0 10a4.5 4 0 0 1 9 0z" fill="#cfcfcf"/></svg>My Account</span>
    <span><svg width="10" height="9" viewBox="0 0 10 9"><path d="M1 5l3 3 5-7" stroke="#cfcfcf" stroke-width="1.8" fill="none"/></svg>Checkout</span>
    <span class="login"><svg width="8" height="10" viewBox="0 0 8 10"><rect x="0" y="4" width="8" height="6" fill="#9bcb3c"/><path d="M2 4V2.5a2 2 0 0 1 4 0V4" stroke="#9bcb3c" fill="none"/></svg>Log In</span>
  </div>
  <div class="abs hotline"><span class="badge">24</span>hour messaging service on :</div>
  <div class="abs hotline-nums">0139-555-0127<i>•</i>0845-555-0193</div>
  <div class="abs search"><div class="field">Search here...</div><div class="btn">SEARCH</div></div>
  <div class="abs cart">
    <div class="label"><svg width="14" height="12" viewBox="0 0 14 12"><path d="M0 1h3l2 7h7l2-5H4" stroke="#fff" stroke-width="1.5" fill="none"/><circle cx="6" cy="11" r="1" fill="#fff"/><circle cx="11" cy="11" r="1" fill="#fff"/></svg>CART <small>2 Items</small></div>
    <div class="cur">£</div>
  </div>
  <nav class="abs nav">
    <a>SHOP</a><a class="active">ABOUT US</a><a>GROUND SOLUTIONS</a><a>PONDERMESH</a><a>CONTACT US</a>
  </nav>
</header>

<!-- categories -->
<aside class="abs categories">
  <div class="cat-head"><svg width="14" height="11" viewBox="0 0 14 11"><rect y="0" width="14" height="2" fill="#fff"/><rect y="4.5" width="14" height="2" fill="#fff"/><rect y="9" width="14" height="2" fill="#fff"/></svg>CATEGORIES</div>
  <ul class="cat-list">
    <li>Lorem ipsum dolor<svg width="13" height="13" viewBox="0 0 13 13"><circle cx="6.5" cy="6.5" r="6" fill="none" stroke="#aaa"/><path d="M5.5 4l2.5 2.5-2.5 2.5" stroke="#888" fill="none"/></svg></li>
    <li class="current">Sit amet consectetuer<svg width="13" height="13" viewBox="0 0 13 13"><circle cx="6.5" cy="6.5" r="6" fill="none" stroke="#aaa"/><path d="M5.5 4l2.5 2.5-2.5 2.5" stroke="#888" fill="none"/></svg></li>
    <li>Adipiscing elit sed<svg width="13" height="13" viewBox="0 0 13 13"><circle cx="6.5" cy="6.5" r="6" fill="none" stroke="#aaa"/><path d="M5.5 4l2.5 2.5-2.5 2.5" stroke="#888" fill="none"/></svg></li>
    <li>Diam nonummy nibh euismod<svg width="13" height="13" viewBox="0 0 13 13"><circle cx="6.5" cy="6.5" r="6" fill="none" stroke="#aaa"/><path d="M5.5 4l2.5 2.5-2.5 2.5" stroke="#888" fill="none"/></svg></li>
    <li>Tincidunt ut laoreet dolore<svg width="13" height="13" viewBox="0 0 13 13"><circle cx="6.5" cy="6.5" r="6" fill="none" stroke="#aaa"/><path d="M5.5 4l2.5 2.5-2.5 2.5" stroke="#888" fill="none"/></svg></li>
    <li>Magna aliquam erat volutpat<svg width="13" height="13" viewBox="0 0 13 13"><circle cx="6.5" cy="6.5" r="6" fill="none" stroke="#aaa"/><path d="M5.5 4l2.5 2.5-2.5 2.5" stroke="#888" fill="none"/></svg></li>
    <li>Ut wisi enim ad minim veniam<svg width="13" height="13" viewBox="0 0 13 13"><circle cx="6.5" cy="6.5" r="6" fill="none" stroke="#aaa"/><path d="M5.5 4l2.5 2.5-2.5 2.5" stroke="#888" fill="none"/></svg></li>
    <li>Lorem ipsum dolor<svg width="13" height="13" viewBox="0 0 13 13"><circle cx="6.5" cy="6.5" r="6" fill="none" stroke="#aaa"/><path d="M5.5 4l2.5 2.5-2.5 2.5" stroke="#888" fill="none"/></svg></li>
    <li>Sit amet consectetuer<svg width="13" height="13" viewBox="0 0 13 13"><circle cx="6.5" cy="6.5" r="6" fill="none" stroke="#aaa"/><path d="M5.5 4l2.5 2.5-2.5 2.5" stroke="#888" fill="none"/></svg></li>
    <li>Adipiscing elit sed<svg width="13" height="13" viewBox="0 0 13 13"><circle cx="6.5" cy="6.5" r="6" fill="none" stroke="#aaa"/><path d="M5.5 4l2.5 2.5-2.5 2.5" stroke="#888" fill="none"/></svg></li>
  </ul>
</aside>

<!-- hero -->
<section class="abs slider">
  <div class="photo" role="img" aria-label="Gravel-filled black grid cells forming a pathway"></div>
  <div class="abs slide-caption">GRAVELGRID SYSTEM FOR PATHWAYS</div>
  <div class="abs slide-arrow" style="left:14px">‹</div>
  <div class="abs slide-arrow" style="right:14px">›</div>
  <div class="abs slide-dots"><b></b><b class="on"></b><b></b><b></b></div>
</section>
<section class="abs promo" role="img" aria-label="Green paving grid laid on grass">
  <h2>STABILISED GRAVEL PAVING GRIDS</h2>
  <p>Magna aliquam erat volutpat</p>
  <div class="shop">SHOP NOW</div>
</section>

<!-- news -->
<section class="abs panel news">
  <div class="panel-title">LATEST <em>NEWS</em></div>
  <div class="pager"><span>‹</span><span>›</span></div>
  <div class="panel-rule"></div>
  <div class="photo" role="img" aria-label="Large family house with a gravel driveway"></div>
  <h3>SIT AMET CONSECTETUER</h3>
  <div class="meta">▦ July 22, 2016<br>● Comments<span class="likes">♥ 16</span></div>
  <p>Lorem ipsum dolor sit amet, consectetuer adipiscing elit, sed diam nonummy nibh euismod tincidunt ut laoreet dolore magna aliquam erat volutpat. ullamcorper suscipit lobortis nisl ut aliquip ex ea commodo consequat.</p>
  <span class="read-more">READ MORE</span>
</section>

<!-- popular -->
<section class="abs panel popular">
  <div class="panel-title">POPULAR <em>CHOICE</em></div>
  <div class="pager"><span>‹</span><span>›</span></div>
  <div class="panel-rule"></div>
  <svg class="hex" width="157" height="196" viewBox="0 0 184 207" role="img" aria-label="Turf and grass reinforcement mesh filled with gravel">
    <polygon points="92,2 180,52 180,155 92,205 4,155 4,52" fill="#9bcb3c"/>
    <polygon points="92,11 172,57 172,150 92,196 12,150 12,57" fill="#fff"/>
    <polygon points="92,16 168,60 168,147 92,191 16,147 16,60" fill="url(#gravel)"/>
  </svg>
  <div class="name">TURF/GRASS REINFORCEMENT<br>MESH</div>
  <div class="price">£ 100.00</div>
  <div class="deal"><div class="order">ORDER NOW</div><div class="off">20 % OFF</div></div>
</section>

<!-- new products -->
<section class="abs panel products new">
  <div class="panel-title">NEW <em>PRODUCTS</em></div>
  <div class="pager"><span>‹</span><span>›</span></div>
  <div class="panel-rule"></div>
  <div class="grid">
    <div class="card">
      <svg width="184" height="207" viewBox="0 0 184 207" role="img" aria-label="Green cellular grid under turf, shown in cross-section"><polygon points="92,2 180,52 180,155 92,205 4,155 4,52" fill="#f78f20"/><polygon points="92,11 172,57 172,150 92,196 12,150 12,57" fill="#fff"/><polygon points="92,16 168,60 168,147 92,191 16,147 16,60" fill="url(#turf)"/></svg>
      <div class="name">PONDERMESH GS PRO<br>( BLACK )</div>
      <div class="buy"><div class="shop">SHOP NOW</div><div class="price">£ 10.50</div></div>
    </div>
    <div class="card">
      <svg width="184" height="207" viewBox="0 0 184 207" role="img" aria-label="Black reinforcement mesh with gravel"><polygon points="92,2 180,52 180,155 92,205 4,155 4,52" fill="#9bcb3c"/><polygon points="92,11 172,57 172,150 92,196 12,150 12,57" fill="#fff"/><polygon points="92,16 168,60 168,147 92,191 16,147 16,60" fill="url(#mesh)"/></svg>
      <div class="hover-tag"><svg width="13" height="11" viewBox="0 0 14 12"><path d="M0 1h3l2 7h7l2-5H4" stroke="#fff" stroke-width="1.5" fill="none"/><circle cx="6" cy="11" r="1" fill="#fff"/><circle cx="11" cy="11" r="1" fill="#fff"/></svg><br>£ 125.00<small>View Details</small></div>
      <div class="name">TURF/GRASS REINFORCEMENT<br>MESH</div>
      <div class="buy"><div class="shop">SHOP NOW</div><div class="price">£ 10.50</div></div>
    </div>
    <div class="card">
      <svg width="184" height="207" viewBox="0 0 184 207" role="img" aria-label="Vehicle tyre on a gravel grid surface"><polygon points="92,2 180,52 180,155 92,205 4,155 4,52" fill="#f78f20"/><polygon points="92,11 172,57 172,150 92,196 12,150 12,57" fill="#fff"/><polygon points="92,16 168,60 168,147 92,191 16,147 16,60" fill="url(#tyre)"/></svg>
      <div class="name">PONDERMESH 40 PRO SYSTEM</div>
      <div class="buy"><div class="shop">SHOP NOW</div><div class="price">£ 10.50</div></div>
    </div>
    <div class="card">
      <svg width="184" height="207" viewBox="0 0 184 207" role="img" aria-label="Green cellular grid under turf, shown in cross-section"><polygon points="92,2 180,52 180,155 92,205 4,155 4,52" fill="#f78f20"/><polygon points="92,11 172,57 172,150 92,196 12,150 12,57" fill="#fff"/><polygon points="92,16 168,60 168,147 92,191 16,147 16,60" fill="url(#turf)"/></svg>
      <div class="name">PONDERMESH GS PRO<br>( BLACK )</div>
      <div class="buy"><div class="shop">SHOP NOW</div><div class="price">£ 10.50</div></div>
    </div>
    <div class="card">
      <svg width="184" height="207" viewBox="0 0 184 207" role="img" aria-label="Reinforcement mesh filled with gravel"><polygon points="92,2 180,52 180,155 92,205 4,155 4,52" fill="#9bcb3c"/><polygon points="92,11 172,57 172,150 92,196 12,150 12,57" fill="#fff"/><polygon points="92,16 168,60 168,147 92,191 16,147 16,60" fill="url(#gravel)"/></svg>
      <div class="name">TURF/GRASS REINFORCEMENT<br>MESH</div>
      <div class="buy"><div class="shop">SHOP NOW</div><div class="price">£ 10.50</div></div>
    </div>
    <div class="card">
      <svg width="184" height="207" viewBox="0 0 184 207" role="img" aria-label="Vehicle tyre on a gravel grid surface"><polygon points="92,2 180,52 180,155 92,205 4,155 4,52" fill="#f78f20"/><polygon points="92,11 172,57 172,150 92,196 12,150 12,57" fill="#fff"/><polygon points="92,16 168,60 168,147 92,191 16,147 16,60" fill="url(#tyre)"/></svg>
      <div class="name">PONDERMESH 40 PRO SYSTEM</div>
      <div class="buy"><div class="shop">SHOP NOW</div><div class="price">£ 10.50</div></div>
    </div>
  </div>
</section>

<div class="abs stripe" style="left:97px;top:1407px;width:1006px"></div>

<!-- testimonials -->
<section class="abs panel testimonials">
  <div class="panel-title">TESTIMONIALS</div>
  <div class="pager"><span>‹</span><span>›</span></div>
  <div class="panel-rule"></div>
  <svg class="avatar" width="105" height="104" viewBox="0 0 105 104" role="img" aria-label="Customer portrait">
    <polygon points="52.5,2 101,27 101,77 52.5,102 4,77 4,27" fill="#fff"/>
    <circle cx="52.5" cy="52" r="38" fill="url(#portrait)"/>
  </svg>
  <div class="quote">“</div>
  <p>Wasn't sure where to compliment. I just wanted to say i am so happy to be your customer. You make my life so easy, thanks for your great service.</p>
  <div class="who"><b>Ewan Dorsey</b>, Manager<br>XYZ Company</div>
</section>

<!-- featured products -->
<section class="abs panel products featured">
  <div class="panel-title">FEATURED <em>PRODUCTS</em></div>
  <div class="pager"><span>‹</span><span>›</span></div>
  <div class="panel-rule"></div>
  <div class="grid">
    <div class="card">
      <svg width="184" height="207" viewBox="0 0 184 207" role="img" aria-label="Green cellular grid under turf, shown in cross-section"><polygon points="92,2 180,52 180,155 92,205 4,155 4,52" fill="#f78f20"/><polygon points="92,11 172,57 172,150 92,196 12,150 12,57" fill="#fff"/><polygon points="92,16 168,60 168,147 92,191 16,147 16,60" fill="url(#turf)"/></svg>
      <div class="name">PONDERMESH GS PRO<br>( BLACK )</div>
      <div class="buy"><div class="shop">SHOP NOW</div><div class="price">£ 10.50</div></div>
    </div>
    <div class="card">
      <svg width="184" height="207" viewBox="0 0 184 207" role="img" aria-label="Black reinforcement mesh with gravel"><polygon points="92,2 180,52 180,155 92,205 4,155 4,52" fill="#9bcb3c"/><polygon points="92,11 172,57 172,150 92,196 12,150 12,57" fill="#fff"/><polygon points="92,16 168,60 168,147 92,191 16,147 16,60" fill="url(#mesh)"/></svg>
      <div class="hover-tag"><svg width="13" height="11" viewBox="0 0 14 12"><path d="M0 1h3l2 7h7l2-5H4" stroke="#fff" stroke-width="1.5" fill="none"/><circle cx="6" cy="11" r="1" fill="#fff"/><circle cx="11" cy="11" r="1" fill="#fff"/></svg><br>£ 125.00<small>View Details</small></div>
      <div class="name">TURF/GRASS REINFORCEMENT<br>MESH</div>
      <div class="buy"><div class="shop">SHOP NOW</div><div class="price">£ 10.50</div></div>
    </div>
    <div class="card">
      <svg width="184" height="207" viewBox="0 0 184 207" role="img" aria-label="Vehicle tyre on a gravel grid surface"><polygon points="92,2 180,52 180,155 92,205 4,155 4,52" fill="#f78f20"/><polygon points="92,11 172,57 172,150 92,196 12,150 12,57" fill="#fff"/><polygon points="92,16 168,60 168,147 92,191 16,147 16,60" fill="url(#tyre)"/></svg>
      <div class="name">PONDERMESH 40 PRO SYSTEM</div>
      <div class="buy"><div class="shop">SHOP NOW</div><div class="price">£ 10.50</div></div>
    </div>
  </div>
</section>

<!-- about & clients -->
<section class="abs about">
  <h2 class="section-head">ABOUT <em>US</em></h2>
  <p>Lorem ipsum dolor sit amet, consectetuer adipiscing elit, sed diam nonummy nibh euismod tincidunt ut laoreet dolore magna aliquam erat volutpat.</p>
  <span class="read-more">READ MORE</span>
</section>
<section class="abs clients">
  <h2 class="section-head">OUR <em>CLIENTS</em></h2>
  <div class="client-row">
    <span class="client-arrow" style="left:12px">‹</span>
    <span class="client" style="left:52px">Halvern<small>fresh solutions</small></span>
    <span class="client" style="left:238px">Solace<small>interiors</small></span>
    <span class="client" style="left:396px">Vareto<small>home design</small></span>
    <span class="client" style="left:578px">Quarra<small>real estate company</small></span>
    <span class="client-arrow" style="left:726px">›</span>
  </div>
</section>

<!-- footer -->
<footer>
  <div class="abs footer"></div>
  <section class="abs newsletter">
    <h2>OUR NEWSLETTER</h2>
    <div class="field">Enter your ID</div>
    <div class="btn">✉ SUBSCRIBE</div>
    <div class="social" aria-label="Social links">
      <svg width="38" height="42" viewBox="0 0 38 42"><polygon points="19,1 37,11 37,31 19,41 1,31 1,11" fill="#fff"/></svg>
      <svg width="38" height="42" viewBox="0 0 38 42"><polygon points="19,1 37,11 37,31 19,41 1,31 1,11" fill="#fff"/></svg>
      <svg width="38" height="42" viewBox="0 0 38 42"><polygon points="19,1 37,11 37,31 19,41 1,31 1,11" fill="#fff"/></svg>
      <svg width="38" height="42" viewBox="0 0 38 42"><polygon points="19,1 37,11 37,31 19,41 1,31 1,11" fill="#fff"/></svg>
    </div>
  </section>

  <section class="abs foot-col sitemap">
    <h3>SITE MAP</h3>
    <div class="cols">
      <ul><li>Shop</li><li class="current">About us</li><li>Ground Solutions</li><li>Pondermesh</li><li>Request a Quote</li><li>Contact Us</li></ul>
      <ul><li>Gallery</li><li>Customer Service</li><li>My Account</li><li>Delivery and Returns</li><li>Terms &amp; Conditions</li><li>Privacy Policy</li></ul>
    </div>
  </section>

  <section class="abs foot-col portfolio">
    <h3>RECENT PORTFOLIO</h3>
    <div class="thumbs">
      <div role="img" aria-label="Gravel path project" style="background:#8d8377"></div>
      <div role="img" aria-label="Brick driveway project" style="background:#8a5a48"></div>
      <div role="img" aria-label="Paving project" style="background:#7b7a78"></div>
      <div role="img" aria-label="Garden path project" style="background:#6f7f63"></div>
      <div role="img" aria-label="Stone paving project" style="background:#b4aea5"></div>
      <div role="img" aria-label="Car park project" style="background:#5b5a5c"></div>
      <div role="img" aria-label="Gravel grid detail" style="background:#9e9890"></div>
      <div role="img" aria-label="Vehicle on grid surface" style="background:#3a4a78"></div>
    </div>
    <div class="view">View all</div>
  </section>

  <section class="abs foot-col contact">
    <h3>CONTACT INFO</h3>
    <ul>
      <li><svg width="10" height="14" viewBox="0 0 10 14"><path d="M5 0a5 5 0 0 1 5 5c0 4-5 9-5 9S0 9 0 5a5 5 0 0 1 5-5z" fill="#f78f20"/><circle cx="5" cy="5" r="2" fill="#333"/></svg><span>Harrowfield House, Brackenmoor Ind Est,<br>Kelvinford, G99 4XT.</span></li>
      <li><svg width="12" height="12" viewBox="0 0 12 12"><path d="M0 6l12-6-4 12-2-5z" fill="#f78f20"/></svg><span>sales@pondermeshpaths.co.uk</span></li>
      <li><svg width="12" height="12" viewBox="0 0 12 12"><circle cx="6" cy="6" r="5.2" fill="none" stroke="#f78f20" stroke-width="1.5"/><path d="M6 3v3.5h2.5" stroke="#f78f20" fill="none"/></svg><span>Mon to Fri - 9:00am to 6:00pm</span></li>
    </ul>
    <div class="cards"><span>Cardo</span><span>Findra</span><span>Paylo</span><span>Nimbo</span><span>Vexa</span></div>
  </section>

  <section class="abs service">
    <div class="big">24<em>/</em>7</div>
    <div class="tag">MESSAGING SERVICE</div>
    <div class="nums">0139-555-0127<br>0845-555-0193</div>
  </section>

  <div class="abs stripe bottom-stripe"></div>
  <div class="abs copyright">© 2016. www.pondermeshpaths.co.uk.  All rights reserved.</div>
</footer>

</body>
</html>
```